Business Card Design

Lintel PR is a public relations consultancy service for the self build, home refurbishment and home improvement market.
It represents everything about 'home' so envisage logo featuring maybe roof pitch over the 'A' of Lintel. Colour/font undecided.

Industry/Entity Type

Home Improvement

Contact Information for Business Card

Fenna Corrowdale
fenna@lintelpr-mail.co.uk
Telephone Direct: 0712 645 8219

```html
<!DOCTYPE html>
<html lang="en">
<head>
<meta charset="utf-8">
<title>Lintel PR – Business Card</title>
<link rel="stylesheet" href="https://fonts.googleapis.com/css2?family=PT+Sans&family=Arimo&display=swap">
<style>
  :root {
    --paper: #e9ecec;
    --paper-edge: #dde1e1;
    --rail: #4b1a0d;
    --wood-dark: #7a2410;
    --wood-mid: #a5381a;
    --wood-light: #b9481f;
    --ink: #5a1a0e;
    --contact: #3b1a10;
  }
  html, body {
    margin: 0;
    padding: 0;
    overflow: hidden;
    background: #ffffff;
  }
  .card {
    position: relative;
    width: 1200px;
    height: 668px;
    overflow: hidden;
    background: radial-gradient(ellipse at 50% 45%, var(--paper) 60%, var(--paper-edge) 100%);
  }
  .rail {
    position: absolute;
    left: 0;
    width: 1200px;
    height: 8px;
    background: linear-gradient(to bottom, #6a2814 0%, var(--rail) 50%, #2e0f06 100%);
  }
  .rail--top { top: 80px; }
  .rail--bottom { top: 562px; }
  .timber {
    position: absolute;
    top: 0;
    width: 62px;
    height: 668px;
    background: linear-gradient(to right, var(--wood-dark) 0%, var(--wood-mid) 30%, var(--wood-light) 55%, var(--wood-mid) 80%, var(--wood-dark) 100%);
  }
  .timber--left { left: 94px; }
  .timber--right { left: 1044px; }
  .brand {
    position: absolute;
    top: 150px;
    left: 0;
    width: 1200px;
    margin: 0;
    text-align: center;
    font-family: "PT Sans", sans-serif;
    font-weight: 400;
    font-size: 120px;
    line-height: 1;
    color: var(--ink);
  }
  .person {
    position: absolute;
    top: 455px;
    left: 0;
    width: 1200px;
    margin: 0;
    text-align: center;
    font-family: "PT Sans", sans-serif;
    font-weight: 400;
    font-size: 56px;
    line-height: 1;
    color: var(--ink);
  }
  .contact {
    position: absolute;
    top: 601px;
    left: 214px;
    margin: 0;
    font-family: "Arimo", sans-serif;
    font-size: 23px;
    line-height: 1;
    color: var(--contact);
    white-space: nowrap;
  }
  .contact__item + .contact__item { margin-left: 46px; }
</style>
</head>
<body>
  <div class="card">
    <div class="rail rail--top"></div>
    <div class="rail rail--bottom"></div>
    <div class="timber timber--left" role="img" aria-label="Vertical wooden plank with reddish wood grain"></div>
    <div class="timber timber--right" role="img" aria-label="Vertical wooden plank with reddish wood grain"></div>

    <h1 class="brand">Lintel PR</h1>
    <p class="person">Fenna Corrowdale</p>
    <p class="contact">
      <span class="contact__item">Telephone Direct: 0712 645 8219</span><span class="contact__item">fenna@lintelpr-mail.co.uk</span>
    </p>
  </div>
</body>
</html>
```